Trucking Company Website Design

We are working with a Trucking company in California. They provide trucking services for dirt, gravel, landscape bark, and landscape materials.

As you might imagine, there are no websites we could find for inspiration for trucking companies.

Thank you for taking the time to consider designing a website for us. We are web developers based in Stockton, CA, USA. Most of our projects go through the same process. Understanding this process may help you win a project with us. We custom-code all of our websites in-house. We don’t have any requirements as to what tools you use for your design, but we ask that you follow these guidelines.

IMAGES:
If you use any images or icons in the design, we ask that you have a link to the asset so we can purchase the image/icon. Most of the designs we submit do not have the customer’s images on them unless they have some great images. Be creative; show us the feeling you are trying to portray with your image choices. Use any royalty-free site you choose. We subscribe to Quillo and mainly use their images, but we can purchase images outside of Quillo. PLEASE NOTE: we will not submit designs to clients with watermarks on the images.

FONTS:
We ask that you identify the fonts you’re using in the design. This can be done in a message if you want. We typically use Varnex Fonts and Quillo Fonts.

CONTENT:
We're always open to different content and ideas. We often submit designs with stock images so the client can see our vision. We typically take pictures after the website launch to use their images with our vision. Lorem Ipsum is fine for paragraphs, but we ask that you make the Headers with correct English. We want to be able to show the vision and identify the sections of the website.

INSPIRATION:
We typically add a couple of links in the brief of websites we like to help you get started in your design.

REVISIONS:
We do not often ask for revisions of the designs unless we see something in the design that may not appeal to the client. If there are slight changes that we want to make, we do that in the development process.

FEEDBACK:
We rarely give feedback on designs during the design process. We are working on many website projects and do not have the time to provide feedback. We usually respond if your request is well thought out and asks specific questions, but a note asking “feedback, please” usually goes unanswered.

```html
<!DOCTYPE html>
<html lang="en">
<head>
<meta charset="utf-8">
<title>Summit Haul – Trucking</title>
<link href="https://fonts.googleapis.com/css2?family=Poppins:ital,wght@0,300;0,400;0,500;0,600;0,700;0,800;1,400&display=swap" rel="stylesheet">
<style>
:root{
  --blue:#1a8bc4;
  --blue-dark:#1a78b2;
  --red:#e8303a;
  --ink:#333;
  --muted:#555;
  --footer:#333333;
  --footer-dark:#2a2a2a;
}
*{box-sizing:border-box;margin:0;padding:0}
html,body{width:1200px;height:3692px;overflow:hidden}
body{font-family:'Poppins',sans-serif;color:var(--ink);background:#fff;position:relative}
.abs{position:absolute}
.brand{font-weight:700;color:var(--blue);font-size:34px;letter-spacing:.5px;display:flex;align-items:center;gap:12px}
.brand .mark{width:30px;height:30px;background:var(--red)}
.header .brand{left:75px;top:26px}
.call{left:648px;top:26px;display:flex;align-items:center;gap:10px}
.call .ico{width:38px;height:38px;border:2px solid var(--blue);border-radius:50%;display:flex;align-items:center;justify-content:center}
.call small{display:block;color:var(--red);font-weight:600;font-size:13px}
.call b{display:block;color:var(--blue);font-size:25px;font-weight:600;line-height:1}
.quote{left:923px;top:24px;width:204px;height:44px;border:2px solid var(--red);color:var(--red);font-weight:600;font-size:14px;display:flex;align-items:center;justify-content:center}
.nav{left:0;top:92px;width:1200px;height:60px;background:var(--blue);display:flex;align-items:center;padding-left:75px}
.nav a{color:#fff;text-decoration:none;font-weight:600;font-size:16px;height:60px;display:flex;align-items:center;margin-right:71px}
.nav a.active{background:var(--red);padding:0 30px;margin-right:36px}
.hero{left:0;top:152px;width:1200px;height:629px;background:linear-gradient(180deg,#7d7468 0%,#c29058 30%,#9a9285 60%,#6b5f4b 100%)}
.hero-panel{left:703px;top:295px;width:424px;height:345px;background:rgba(255,255,255,.82);text-align:center;padding-top:40px}
.hero-panel h1{font-weight:400;font-size:37px;letter-spacing:1px;color:#222}
.hero-panel p{font-size:24px;line-height:35px;margin-top:6px;color:#333}
.btn-red{display:inline-block;background:var(--red);color:#fff;font-size:18px;padding:18px 35px;margin-top:28px}
.dots{display:flex;gap:9px;justify-content:center;margin-top:52px}
.dots i{width:10px;height:10px;border-radius:50%;background:#333}
.dots i:first-child{background:var(--blue)}
.sec-title{left:0;width:1200px;text-align:center;font-size:37px;font-weight:400;color:var(--blue);letter-spacing:1px}
.sec-title .mark{display:inline-block;width:30px;height:40px;background:var(--red);clip-path:polygon(0 0,55% 0,100% 50%,55% 100%,0 100%,40% 50%);vertical-align:middle;margin-left:8px}
.sec-desc{left:0;width:1200px;text-align:center;font-size:17px;color:#444}
.card{top:983px;width:242px;height:294px;color:#fff}
.card .cap{position:absolute;left:18px;bottom:18px;font-weight:800;font-size:22px;line-height:25px}
.card .arr{position:absolute;right:18px;bottom:30px}
.about{left:0;top:1357px;width:1200px;height:507px;background:var(--blue-dark)}
.about-img{left:622px;top:1357px;width:578px;height:507px;background:linear-gradient(160deg,#8aa0b4,#b74a40 55%,#5b5f62);clip-path:polygon(0 100%,260px 0,578px 0,578px 100%)}
.about-img2{left:622px;top:1357px;width:578px;height:507px;background:var(--blue-dark);clip-path:polygon(0 100%,260px 0,0 0)}
.about h2{position:absolute;left:75px;top:68px;color:#fff;font-weight:400;font-size:37px}
.about p{position:absolute;left:75px;top:130px;width:600px;color:#fff;font-size:17.5px;line-height:31.5px}
.btn-line{position:absolute;left:75px;top:383px;width:179px;height:58px;border:2px solid #fff;color:#fff;font-size:18px;display:flex;align-items:center;justify-content:center}
.date{color:var(--red);font-weight:600;font-size:17px}
.ntitle{color:var(--blue);font-size:23px;line-height:30px;font-weight:500}
.ntext{color:#444;font-size:17px;line-height:27px}
.testi{left:0;top:2693px;width:1200px;height:482px;background:linear-gradient(90deg,#2b5fa0,#7a5a8c 50%,#e8404a)}
.testi h2{position:absolute;width:1200px;text-align:center;top:65px;color:#fff;font-weight:400;font-size:37px}
.tcard{top:157px;width:328px;height:230px;background:#fff;border-radius:8px;text-align:center;padding:30px 25px}
.tcard p{font-style:italic;font-size:15px;line-height:26px;color:#444}
.tcard b{display:block;color:var(--red);font-size:14px;font-weight:700;margin-top:14px}
.tcard .q{position:absolute;left:142px;bottom:-22px;width:44px;height:44px;border-radius:50%;background:var(--blue);color:#fff;font-weight:800;font-size:30px;line-height:52px}
.news-t{left:73px;top:3218px;color:var(--blue);font-size:37px;font-weight:400}
.news-t .mark{display:inline-block;width:30px;height:40px;background:var(--red);clip-path:polygon(0 0,55% 0,100% 50%,55% 100%,0 100%,40% 50%);vertical-align:middle;margin-left:6px}
.email{left:525px;top:3212px;width:508px;height:56px;border:1px solid #ccc;font-size:15px;color:#555;padding:18px 18px}
.signup{left:1031px;top:3212px;width:96px;height:56px;background:var(--red);color:#fff;font-weight:600;font-size:15px;display:flex;align-items:center;justify-content:center;clip-path:polygon(0 0,100% 0,100% 100%,0 100%,8px 50%)}
.footer{left:0;top:3303px;width:1200px;height:325px;background:var(--footer);color:#fff}
.footer .brand{position:absolute;left:75px;top:140px;font-size:36px}
.fcol{position:absolute;top:60px;border-left:1px solid #555;height:210px;padding-left:20px}
.fcol h4{font-weight:400;font-size:20px;letter-spacing:.5px}
.fcol a{color:#eee;font-size:15px;text-decoration:none}
.links{display:grid;grid-template-columns:126px 100px;row-gap:24px;margin-top:27px}
.info div{font-size:15.5px;line-height:28px;display:flex;gap:14px;margin-top:14px}
.info .i{width:18px;flex:none;color:var(--blue)}
.social{display:flex;gap:9px;margin-top:24px}
.social i{width:33px;height:33px;border:2px solid #ddd;border-radius:50%}
.copy{left:0;top:3628px;width:1200px;height:64px;background:var(--footer-dark);color:#fff;font-size:14px;text-align:center;line-height:64px}
</style>
</head>
<body>
<header class="header">
  <div class="brand abs"><span>SUMMIT HAUL</span><span class="mark"></span></div>
  <div class="call abs">
    <div class="ico"><svg width="18" height="18" viewBox="0 0 24 24"><path d="M6.6 10.8a15 15 0 0 0 6.6 6.6l2.2-2.2a1 1 0 0 1 1-.25 11 11 0 0 0 3.6.6 1 1 0 0 1 1 1V20a1 1 0 0 1-1 1A17 17 0 0 1 3 4a1 1 0 0 1 1-1h3.5a1 1 0 0 1 1 1c0 1.25.2 2.45.6 3.6a1 1 0 0 1-.25 1z" fill="#333"/></svg></div>
    <div><small>CALL US</small><b>+1 555-014-2880</b></div>
  </div>
  <div class="quote abs">REQUEST A QUOTE</div>
</header>
<nav class="nav abs">
  <a class="active">HOME</a><a>ABOUT US</a><a>SERVICES</a><a>GALLERY</a><a>BLOG</a><a>TESTIMONIALS</a><a>CONTACT US</a>
</nav>

<section class="hero abs" role="img" aria-label="Dump truck driving on a dirt road through fields at sunset"></section>
<div class="hero-panel abs">
  <h1>SUMMIT HAUL</h1>
  <p>We are a trucking company<br>based in california</p>
  <span class="btn-red">READ MORE</span>
  <div class="dots"><i></i><i></i><i></i><i></i></div>
</div>

<h2 class="sec-title abs" style="top:850px">OUR SERVICES<span class="mark"></span></h2>
<p class="sec-desc abs" style="top:925px">Excepteur sint occaecat cupidatat non proident, sunt in culpa qui officia deserunt mollit.</p>
<div class="card abs" style="left:75px;background:linear-gradient(180deg,#7b8a55,#8a6a48 50%,#222)" role="img" aria-label="Dump truck loading dirt">
  <div class="cap">DIRT<br>MATERIAL</div><svg class="arr" width="12" height="18" viewBox="0 0 12 18"><path d="M2 2l7 7-7 7" stroke="#fff" stroke-width="3" fill="none"/></svg></div>
<div class="card abs" style="left:345px;background:linear-gradient(180deg,#9aa8b4,#6d6a64 50%,#222)" role="img" aria-label="Truck unloading gravel">
  <div class="cap">GRAVEL<br>MATERIAL</div><svg class="arr" width="12" height="18" viewBox="0 0 12 18"><path d="M2 2l7 7-7 7" stroke="#fff" stroke-width="3" fill="none"/></svg></div>
<div class="card abs" style="left:615px;background:linear-gradient(180deg,#3f6a2a,#4a3a2a 50%,#1a1a1a)" role="img" aria-label="Gloved hand holding landscape bark">
  <div class="cap">LANDSCAPE<br>BARK</div><svg class="arr" width="12" height="18" viewBox="0 0 12 18"><path d="M2 2l7 7-7 7" stroke="#fff" stroke-width="3" fill="none"/></svg></div>
<div class="card abs" style="left:885px;background:linear-gradient(180deg,#b89a78,#8a6e58 50%,#1e1e1e)" role="img" aria-label="Worker laying landscape stones">
  <div class="cap">LANDSCAPE<br>MATERIAL</div><svg class="arr" width="12" height="18" viewBox="0 0 12 18"><path d="M2 2l7 7-7 7" stroke="#fff" stroke-width="3" fill="none"/></svg></div>

<section class="about abs">
  <h2>ABOUT US <span style="display:inline-block;width:30px;height:40px;background:var(--red);clip-path:polygon(0 0,55% 0,100% 50%,55% 100%,0 100%,40% 50%);vertical-align:middle"></span></h2>
  <p>Excepteur sint occaecat cupidatat non proident, sunt in culpa qui officia deserunt mollit. Nemo enim ipsam voluptatem quia voluptas sit aspernatur aut odit aut fugit, sed quia consequuntur magni dolores eos qui ratione voluptatem sequi nesciunt. Neque porro quisquam est, qui dolorem ipsum quia dolor sit amet, consectetur, adipisci velit, sed quia non numquam eius modi tempora incidunt ut labore et dolore magnam aliquam quaerat voluptatem.</p>
  <div class="btn-line">READ MORE</div>
</section>
<div class="about-img abs" role="img" aria-label="Red dump truck on a road among trees"></div>

<h2 class="sec-title abs" style="top:1936px">LATEST NEWS<span class="mark"></span></h2>
<p class="sec-desc abs" style="top:2010px">Excepteur sint occaecat cupidatat non proident, sunt in culpa qui officia deserunt mollit.</p>
<div class="abs" style="left:75px;top:2078px;width:512px;height:360px;background:linear-gradient(180deg,#3c4a52 0%,#5a4030 40%,#6b3e28 100%)" role="img" aria-label="Pile of landscape bark behind a truck"></div>
<div class="abs" style="left:75px;top:2462px;width:512px">
  <div class="date">Jun20, 2023</div>
  <div class="ntitle" style="margin-top:4px">Excepteur sint occaecat cupidatat..</div>
  <div class="ntext" style="margin-top:12px">Sunt in culpa qui officia deserunt mollit&nbsp; exercitationem ullam corporis suscipit laboriosam, nisi ut aliquid ex ea commodi consequatu.</div>
</div>
<div class="abs" style="left:615px;top:2078px;width:242px;height:148px;background:linear-gradient(135deg,#5a7a3a,#8a7050 60%,#b09070)" role="img" aria-label="Dump truck unloading soil"></div>
<div class="abs" style="left:615px;top:2270px;width:242px;height:148px;background:linear-gradient(135deg,#8aa0a8,#6a5a48 55%,#8a3a30)" role="img" aria-label="Excavator loading a truck"></div>
<div class="abs" style="left:615px;top:2462px;width:242px;height:148px;background:linear-gradient(180deg,#9ab0c0,#c8aa78 50%,#b89868)" role="img" aria-label="Piles of sand and gravel"></div>
<div class="abs" style="left:870px;top:2078px;width:257px"><div class="date">Jun20, 2023</div><div class="ntitle">Excepteur sint occaec at cupidatat..</div><div class="ntext" style="margin-top:8px">Sunt in culpa qui officia tionem ullam corporis sucipit</div></div>
<div class="abs" style="left:870px;top:2270px;width:257px"><div class="date">Jun20, 2023</div><div class="ntitle">Excepteur sint occaec at cupidatat..</div><div class="ntext" style="margin-top:8px">Sunt in culpa qui officia tionem ullam corporis sucipit</div></div>
<div class="abs" style="left:870px;top:2462px;width:257px"><div class="date">Jun20, 2023</div><div class="ntitle">Excepteur sint occaec at cupidatat..</div><div class="ntext" style="margin-top:8px">Sunt in culpa qui officia tionem ullam corporis sucipit</div></div>

<section class="testi abs" role="img" aria-label="City skyline with palm trees tinted blue to red">
  <h2>TESTIMONIALS <span style="display:inline-block;width:30px;height:40px;background:var(--red);clip-path:polygon(0 0,55% 0,100% 50%,55% 100%,0 100%,40% 50%);vertical-align:middle"></span></h2>
  <svg class="abs" style="left:30px;top:222px" width="30" height="26" viewBox="0 0 30 26"><path d="M28 13H4M13 3L3 13l10 10" stroke="#fff" stroke-width="4" fill="none"/></svg>
  <svg class="abs" style="left:1138px;top:222px" width="30" height="26" viewBox="0 0 30 26"><path d="M2 13h24M17 3l10 10-10 10" stroke="#fff" stroke-width="4" fill="none"/></svg>
  <div class="tcard abs" style="left:75px"><p>“ Sunt in culpa qui officia deserunt mollit&nbsp; exercitationem ullam corporis suscipit laboriosam, nisi ut aliquid ex ea commodi consequatu.”</p><b>NAME HEADING</b><span class="q">”</span></div>
  <div class="tcard abs" style="left:437px"><p>“ Sunt in culpa qui officia deserunt mollit&nbsp; exercitationem ullam corporis suscipit laboriosam, nisi ut aliquid ex ea commodi consequatu.”</p><b>NAME HEADING</b><span class="q">”</span></div>
  <div class="tcard abs" style="left:799px"><p>“ Sunt in culpa qui officia deserunt mollit&nbsp; exercitationem ullam corporis suscipit laboriosam, nisi ut aliquid ex ea commodi consequatu.”</p><b>NAME HEADING</b><span class="q">”</span></div>
</section>

<h2 class="news-t abs">NEWSLETTER SIGN UP<span class="mark"></span></h2>
<div class="email abs">Email Address</div>
<div class="signup abs">SIGN UP</div>

<footer class="footer abs">
  <div class="brand"><span>SUMMIT HAUL</span><span class="mark"></span></div>
  <div class="fcol" style="left:343px">
    <h4>SITE MAP</h4>
    <div class="links"><a>Home</a><a>Blog</a><a>About Us</a><a>Testimonials</a><a>Services</a><a>Contact Us</a><a>Gallery</a></div>
  </div>
  <div class="fcol info" style="left:612px">
    <h4>CONTACT INFO</h4>
    <div><span class="i">■</span><span>1220 Ridgeview Lane,<br>Stockton, CA 95202</span></div>
    <div><span class="i">✆</span><span>+1 555-014-2880</span></div>
    <div><span class="i">✉</span><span>info@summithaul.com</span></div>
  </div>
  <div class="fcol" style="left:885px;border-left:1px solid #555">
    <h4>FOLLOW US</h4>
    <div class="social"><i></i><i></i><i></i><i></i><i></i></div>
  </div>
</footer>
<div class="copy abs">Copyright © 2023 Company Name All Right Reserved</div>
</body>
</html>
```